indépendant en tant que Massothérapeute et Préparateur Mental, j'ai besoin de ...

Massothérapeute et préparateur mental indépendant, je recherche une carte de visite sobre et dynamique, sans images liées au massage ou à la préparation mentale mais intégrant mon logo. Les couleurs que j'aime bien sont : Blanc, gris, anthracite, noir et jaune

Contact Information for Business Card

carte de préférence Horizontale
neutre qui puisse toucher le deux domaines Massothérapie et préparation mentale

Requirements
Must have
• mon projet doit intégrer au recto:
LOGO
Loïc Bardèze
078 513 26 48
info@loicbardeze.ch
et éventuellement www.loicbardeze.ch

et au verso les deux adresses:

Chemin des Ormilles 7B
1400 Yverdon-les-Bains

Route de la Gravière 9
1700 Fribourg

Should not have
• mon projet ne doit pas contenir d'image en liens avec le massage ni la préparation mentale.

```html
<!DOCTYPE html>
<html lang="fr">
<head>
<meta charset="utf-8">
<title>Loïc Bardèze – Carte de visite</title>
<link rel="stylesheet" href="https://fonts.googleapis.com/css2?family=Work+Sans:wght@400;500;600&display=swap">
<style>
  :root {
    --bg: #141414;
    --card: #1f1f1f;
    --card-edge: #2a2a2a;
    --white: #f4f4f4;
    --grey: #9a9a9a;
    --yellow: #f5b800;
  }
  * { margin: 0; padding: 0; box-sizing: border-box; }
  html, body { width: 1200px; height: 900px; overflow: hidden; }
  body {
    background: radial-gradient(ellipse at 50% 30%, #2a2a2a, var(--bg) 70%);
    font-family: "Work Sans", Arial, sans-serif;
    color: var(--white);
    position: relative;
  }
  .card {
    position: absolute;
    left: 250px;
    width: 700px;
    height: 400px;
    background: var(--card);
    border: 1px solid var(--card-edge);
    box-shadow: 0 18px 40px rgba(0,0,0,.6);
    overflow: hidden;
  }
  .card--verso { top: 35px; }
  .card--recto { top: 465px; }

  .pattern-field {
    position: absolute; inset: 0;
    background: linear-gradient(120deg, #1c1c1c 0%, #242424 45%, #5a5a5a 100%);
  }

  .brand {
    position: absolute;
    display: flex; flex-direction: column; align-items: flex-start;
  }
  .brand__row { display: flex; align-items: center; gap: 10px; }
  .brand__mark { width: 14px; height: 14px; background: var(--white); }
  .brand__name { font-weight: 600; font-size: 24px; letter-spacing: .5px; color: var(--white); }
  .brand__tagline { font-size: 9px; letter-spacing: 1px; text-transform: uppercase; color: var(--white); margin-top: 4px; margin-left: 24px; }

  .card--verso .brand { left: 50%; top: 50%; transform: translate(-50%, -50%); background: var(--card); padding: 14px 20px; }
  .card--recto .brand { left: 48px; top: 168px; }

  .divider { position: absolute; left: 330px; top: 80px; width: 2px; height: 250px; background: var(--yellow); }

  .contact { position: absolute; left: 360px; top: 72px; }
  .contact__name { color: var(--yellow); font-weight: 500; font-size: 30px; letter-spacing: 1px; line-height: 1; }
  .contact__role { font-size: 18px; margin-top: 4px; margin-bottom: 12px; }
  .contact__line { display: flex; align-items: center; gap: 10px; font-size: 18px; line-height: 27px; }
  .contact__line svg { width: 13px; height: 13px; flex: none; }
  .address { font-size: 18px; line-height: 24px; margin-top: 10px; }
</style>
</head>
<body>

<section class="card card--verso">
  <div class="pattern-field" role="img" aria-label="Motif répété du monogramme, gris sur fond anthracite, s'éclaircissant vers la droite"></div>
  <div class="brand">
    <div class="brand__row"><span class="brand__mark"></span><span class="brand__name">Loïc Bardèze</span></div>
    <span class="brand__tagline">Massothérapeute / Préparateur Mental</span>
  </div>
</section>

<section class="card card--recto">
  <div class="brand">
    <div class="brand__row"><span class="brand__mark"></span><span class="brand__name">Loïc Bardèze</span></div>
    <span class="brand__tagline">Massothérapeute / Préparateur Mental</span>
  </div>

  <div class="divider"></div>

  <div class="contact">
    <p class="contact__name">LOÏC BARDÈZE</p>
    <p class="contact__role">Director</p>
    <p class="contact__line">
      <svg viewBox="0 0 24 24" fill="var(--yellow)"><path d="M6.6 10.8a15 15 0 0 0 6.6 6.6l2.2-2.2c.3-.3.7-.4 1-.2 1.1.4 2.3.6 3.6.6.6 0 1 .4 1 1V20c0 .6-.4 1-1 1A17 17 0 0 1 3 4c0-.6.4-1 1-1h3.5c.6 0 1 .4 1 1 0 1.3.2 2.5.6 3.6.1.3 0 .7-.2 1z"/></svg>
      078 513 26 48
    </p>
    <p class="contact__line">
      <svg viewBox="0 0 24 24" fill="none" stroke="var(--yellow)" stroke-width="2.4"><rect x="2" y="5" width="20" height="14" rx="1"/><path d="M2 6l10 7 10-7"/></svg>
      info@loicbardeze.ch
    </p>
    <p class="contact__line">
      <svg viewBox="0 0 24 24" fill="none" stroke="var(--yellow)" stroke-width="2"><circle cx="12" cy="12" r="10"/><path d="M2 12h20M12 2c3 3 3 17 0 20M12 2c-3 3-3 17 0 20"/></svg>
      www.loicbardeze.ch
    </p>
    <p class="address">Chemin des Ormilles 7B<br>1400 Yverdon-les-Bains</p>
    <p class="address">Route de la Gravière 9<br>1700 Fribourg</p>
  </div>
</section>

</body>
</html>
```